Agrarhandel benötigt Homepage
Zielgruppe
Wir sind ein Agrarhandel mit einem Warenumschlagslager im Sinne eines klassischen Einzelhandels und vertreiben Produkte an Landwirte.
Wir vertreiben folgende Hauptproduktgruppen:
Einzelfuttermittel
wie z.B. Sojaexktraktionsschrot. Die einzelnen Produkte könnten z.B. wie die Futtermittel auf folgender Seite dargestellt werden (https://www.kornprobe-beispiel.eu/de/produkt/trelomixan)
Mischfuttermittel
Hier bieten wir unseren Kunden an, individuelles Mischfutter auf Basis unserer Einzelfuttermittel herzustellen.
Weitere Details und weitere Produktbereiche habe ich in einer Powerpoint-Übersicht dargestellt.
Neben diesen Produkten wollen wir uns als Familienunternehmen selbst vorstellen. Zudem betreiben wir in unserer Familie zusätzlich einen Milchviehbetrieb den wir ebenfalls hervorheben möchten, da wir unseren Kunden gegenüber einerseits als Zulieferer aber auch als Kollege auftreten wollen.
Einzelfuttermittel: Hier können wir durch unsere Unabhängigkeit punkten, da wir nicht abhängig von bestimmten Lieferanten sind und dementsprechend unabhängig beraten können. Wir untersuchen im Vergleich zu unseren Wettbewerben die Qualität der Futtermittel bis ins Detail und können daher eine Transparenz bieten, die Konkurrenten in der Regel nicht bieten können. Unser Warenumschlagsplatz mit moderner Technik ermöglicht es uns äußerst kosteneffizient die Waren umschlagen und ausliefern zu können.
Mischfuttermittel: Auf Basis der vorhandenen Einzelfuttermittel stellen wir je nach Kundenwunsch individuelle Mischfutter her. Wir arbeiten mit offenen Deklarationen, sodass unsere Kunden jederzeit nachvollziehen können, ob auch die Einzelfuttermittel verwendet wurden, die sie bestellt haben und keine billigen Ersatzprodukte verwendet wurden.
Zudem sind wir BT und HUPA zertifiziert. Die aktuellen für unser Unternehmen ausgestellten Zertifikate müssen für unsere Kunden als Download zur Verfügung stehen. Statt dem HUPA-Logo bitte das ..
Aufgabenstellung
Wir möchten gerne ein zeitgemäße Homepage, jedoch muss auch berücksichtigt werden, dass unsere Kunden eher konservativ denken.

```html
<!DOCTYPE html>
<html lang="de">
<head>
<meta charset="utf-8">
<title>Talgrund Agrarhandel</title>
<link href="https://fonts.googleapis.com/css2?family=Ubuntu:wght@500;700&family=Open+Sans:ital,wght@0,400;0,600;0,700;1,400&display=swap" rel="stylesheet">
<style>
:root{
  --green:#135a3f;
  --green-dark:#0c3e2b;
  --green-footer:#13684a;
  --yellow:#f4b400;
  --brown:#3b2314;
  --text:#2a2a35;
  --grey:#f1f1f1;
  --red:#d94b4b;
}
*{margin:0;padding:0;box-sizing:border-box}
html,body{width:1200px;height:3562px;overflow:hidden;background:#fff}
body{position:relative;font-family:"Open Sans",sans-serif;color:var(--text);font-size:15px;line-height:20.5px}
.abs{position:absolute}
.topbar{top:0;left:0;width:1200px;height:37px;background:linear-gradient(90deg,var(--green-dark),var(--green));color:#fff;font-size:14px;display:flex;align-items:center;justify-content:flex-end;padding-right:100px;gap:14px}
.phone-dot{width:21px;height:21px;border-radius:50%;background:var(--yellow);display:inline-flex;align-items:center;justify-content:center}
.header{top:37px;left:0;width:1200px;height:101px;background:#fff;border-bottom:1px solid #e6e6e6;z-index:2}
.nav a{position:absolute;top:50px;font-family:"Ubuntu",sans-serif;font-weight:500;font-size:13.5px;color:var(--text);text-decoration:none;letter-spacing:.3px}
.menu-icon{position:absolute;left:1072px;top:50px;width:27px}
.menu-icon span{display:block;height:3px;background:var(--brown);margin-bottom:4px}
.brand-circle{left:502px;top:21px;width:196px;height:196px;border-radius:50%;background:#fff;z-index:3;display:flex;align-items:center;justify-content:center;padding-top:30px;font-family:"Ubuntu",sans-serif;font-weight:700;font-size:21px;color:var(--green);text-align:center;line-height:24px}
.hero{top:138px;left:0;width:1200px;height:549px;background:linear-gradient(180deg,#8e9a95 0%,#6f7d5e 45%,#5b6a3c 70%,#3e3a2c 100%)}
.dots{top:640px;left:575px;display:flex;gap:7px}
.dots span{width:11px;height:11px;border-radius:50%;background:#9a9a9a}
.dots span:first-child{background:#fff}
h2{font-family:"Ubuntu",sans-serif;font-weight:500;color:var(--green);font-size:42px;line-height:56px;text-align:center;letter-spacing:.5px}
.intro{left:350px;width:500px;text-align:justify;text-align-last:center}
.feature{text-align:center;width:220px}
.feature svg{display:block;margin:0 auto 12px}
.feature h3{font-family:"Ubuntu",sans-serif;font-weight:500;font-size:22px;line-height:24px;color:var(--brown);margin-bottom:12px}
.feature p{font-size:14.5px;line-height:19px}
.band{left:0;width:1200px;background:var(--grey)}
.band h4{position:absolute;font-family:"Ubuntu",sans-serif;font-weight:500;font-size:16px;color:var(--green)}
.list{position:absolute;list-style:none}
.list li{display:flex;gap:16px;margin-bottom:11px;font-size:15px;line-height:20px}
.list li svg{flex:none}
.list b{font-weight:700}
.photo2{top:1711px;left:0;width:1200px;height:439px;background:linear-gradient(180deg,#c9c7bf 0%,#9e968a 40%,#6f6454 75%,#a38f6a 100%)}
.footer{top:3138px;left:0;width:1200px;height:339px;background:linear-gradient(90deg,var(--green-dark) 0%,var(--green-footer) 60%,#187455 100%);color:#fff}
.footer .col-line{position:absolute;top:0;width:1px;height:339px;background:rgba(255,255,255,.45)}
.footer h5{position:absolute;font-family:"Ubuntu",sans-serif;font-weight:700;font-size:15px;text-align:center}
.footer .brand{position:absolute;left:90px;top:136px;width:340px;text-align:center;font-family:"Open Sans",sans-serif;font-weight:600;font-size:20px}
.footer .mark{position:absolute;left:234px;top:54px;width:52px;height:52px;border-radius:50%;border:2px solid #fff}
.contact{position:absolute;display:flex;align-items:center;gap:10px;font-size:14px}
.ic{width:21px;height:21px;border-radius:50%;background:var(--yellow);display:inline-flex;align-items:center;justify-content:center}
.copyright{top:3477px;left:0;width:1200px;height:40px;background:#111;color:#fff;font-size:13px;display:flex;align-items:center;justify-content:center}
</style>
</head>
<body>

<div class="abs topbar">
  <span>Jetzt telefonisch beraten lassen</span>
  <span class="phone-dot"><svg width="11" height="11" viewBox="0 0 24 24"><path fill="#3b2314" d="M6.6 10.8a15 15 0 0 0 6.6 6.6l2.2-2.2c.3-.3.7-.4 1-.2 1.1.4 2.3.6 3.6.6.6 0 1 .4 1 1V20c0 .6-.4 1-1 1A17 17 0 0 1 3 4c0-.6.4-1 1-1h3.5c.6 0 1 .4 1 1 0 1.3.2 2.5.6 3.6.1.3 0 .7-.2 1z"/></svg></span>
  <span>09100 555130</span>
</div>

<header class="abs header">
  <nav class="nav">
    <a style="left:100px">EINZELFUTTERMITTEL</a>
    <a style="left:284px">MISCHFUTTERMITTEL</a>
    <a style="left:726px">ÜBER UNS</a>
    <a style="left:831px">UNSER BETRIEB</a>
    <a style="left:970px">KONTAKT</a>
  </nav>
  <div class="menu-icon"><span></span><span></span><span></span></div>
</header>
<div class="abs brand-circle">Talgrund<br>Agrarhandel</div>

<div class="abs hero" role="img" aria-label="Landwirt von hinten auf einer Weide mit grasenden Milchkühen"></div>
<div class="abs dots"><span></span><span></span><span></span></div>

<h2 class="abs" style="top:750px;left:300px;width:600px">FAMILIENBETRIEB MIT<br>TRADITION</h2>
<p class="abs intro" style="top:910px">Wir, die Familie Berger aus Hollstetten bei Marbach, führen einen hochmodernen Milchviehbetrieb und betreiben einen eigenen (Futtermittel-) Agrarhandel. Unser Ziel ist es, die attraktivsten Einzelfuttermittel verschiedener Hersteller anzubieten und bei Bedarf kundenindividuelle Mischfutter in unserer eigenen Mischanlage herzustellen. Diese Vielseitigkeit schätzen unsere Kunden an unserem Betrieb.</p>

<div class="abs feature" style="left:189px;top:1095px">
  <svg width="92" height="86" viewBox="0 0 92 86" fill="none" stroke="#135a3f" stroke-width="3"><path d="M4 84 Q40 50 88 58M10 84 Q44 58 88 66M24 84 Q52 66 88 74M40 84 Q62 74 88 80"/><rect x="28" y="30" width="36" height="14"/><rect x="36" y="20" width="14" height="10"/><path d="M8 4v40M84 4v40M8 12l-5 6M8 12l5 6M84 12l-5 6M84 12l5 6"/></svg>
  <h3>FUTTERMITTEL<br>HERSTELLER</h3>
  <p>Direkte Anbindung an regionale Hersteller und Hersteller aus ganz Europa</p>
</div>
<div class="abs feature" style="left:490px;top:1095px">
  <svg width="92" height="86" viewBox="0 0 92 86" fill="none" stroke="#f4b400" stroke-width="3.5"><path d="M6 44 L46 6 L86 44"/><path d="M16 36v46h60V36"/><rect x="30" y="30" width="12" height="12"/><rect x="50" y="30" width="12" height="12"/><path d="M16 56h60M16 66h60M16 74h60"/></svg>
  <h3>EIGENES<br>LAGERHAUS</h3>
  <p>Das uns ermöglicht eine breite Palette an Futtermittel zu beziehen</p>
</div>
<div class="abs feature" style="left:779px;top:1095px">
  <svg width="92" height="86" viewBox="0 0 92 86" fill="none" stroke="#3b2314" stroke-width="3"><circle cx="26" cy="24" r="19"/><path d="M26 14v10l7 5"/><path d="M45 30h22l16 18v22H12V44"/><path d="M62 30v18h21"/><circle cx="28" cy="72" r="7"/><circle cx="68" cy="72" r="7"/></svg>
  <h3>DIREKTE<br>LIEFERUNG</h3>
  <p>Wir liefern mit eigenen LKWs direkt an unsere Endkunden schnell und kosteneffizient</p>
</div>

<section class="abs band" style="top:1378px;height:295px">
  <h4 style="left:198px;top:37px">Vorteile</h4>
  <ul class="list" style="left:198px;top:82px">
    <li><svg width="29" height="29" viewBox="0 0 30 30"><circle cx="15" cy="15" r="13" fill="none" stroke="#3f9a5a" stroke-width="2"/><path d="M8 15l5 5 9-10" fill="none" stroke="#3f9a5a" stroke-width="2.5"/></svg><span><b>Unabhängig</b>, ohne Beteiligungsstrukturen<br>oder andere vertragliche Abhängigkeiten</span></li>
    <li><svg width="29" height="29" viewBox="0 0 30 30"><circle cx="15" cy="15" r="13" fill="none" stroke="#3f9a5a" stroke-width="2"/><path d="M8 15l5 5 9-10" fill="none" stroke="#3f9a5a" stroke-width="2.5"/></svg><span>Wir verfügen über ein eigenes <b>Lagerhaus</b><br>und können somit <b>europaweit</b> Ware beziehen</span></li>
    <li><svg width="29" height="29" viewBox="0 0 30 30"><circle cx="15" cy="15" r="13" fill="none" stroke="#3f9a5a" stroke-width="2"/><path d="M8 15l5 5 9-10" fill="none" stroke="#3f9a5a" stroke-width="2.5"/></svg><span>Unsere Kunden profitieren von den europa-<br>weiten <b>Preis- und Qualitätsunterschieden</b></span></li>
    <li><svg width="29" height="29" viewBox="0 0 30 30"><circle cx="15" cy="15" r="13" fill="none" stroke="#3f9a5a" stroke-width="2"/><path d="M8 15l5 5 9-10" fill="none" stroke="#3f9a5a" stroke-width="2.5"/></svg><span><b>Individuelle Beratung</b> mit der Möglichkeit von<br><b>kundeninviduellen Mischfutter</b></span></li>
  </ul>
  <ul class="list" style="left:650px;top:82px">
    <li><svg width="29" height="29" viewBox="0 0 30 30"><circle cx="15" cy="15" r="13" fill="none" stroke="#d94b4b" stroke-width="2"/><path d="M10 10l10 10M20 10L10 20" stroke="#d94b4b" stroke-width="2.5"/></svg><span>An keinen Hersteller<br>oder Hafen gebunden</span></li>
    <li><svg width="29" height="29" viewBox="0 0 30 30"><circle cx="15" cy="15" r="13" fill="none" stroke="#d94b4b" stroke-width="2"/><path d="M10 10l10 10M20 10L10 20" stroke="#d94b4b" stroke-width="2.5"/></svg><span>keine aufdringlichen<br>Außendienstler</span></li>
  </ul>
</section>

<div class="abs photo2" role="img" aria-label="Familie spaziert durch einen modernen Milchviehstall zwischen Kühen"></div>

<h2 class="abs" style="top:2220px;left:300px;width:600px">UNSERE<br>QUALITÄTSPOLITIK</h2>
<p class="abs intro" style="top:2378px;left:352px">Als ein <b>BT-zertifiziertes Unternehmen</b> verfolgen wir eine konsequente Qualitätspolitik für unsere Kunden. Dies geschieht durch regelmäßige Untersuchungen unserer Futtermittel. Die Durchschnittswerte dieser Analysen dienen als Grundlage für unsere Futtermitteldeklaration. Dadurch bieten wir unseren Kunden eine zuverlässige Basis für die individuelle Rationsberechnung. Wir streben damit an, den natürlichen Schwankungen und Messtoleranzen gerecht zu werden, die mit der Eigenschaft als Naturprodukt einhergehen.</p>

<div class="abs feature" style="left:363px;top:2572px">
  <svg width="86" height="90" viewBox="0 0 86 90" fill="none"><path d="M8 4h54v78H8z" stroke="#c9c9c9" stroke-width="4"/><circle cx="40" cy="40" r="18" stroke="#135a3f" stroke-width="4"/><path d="M53 53l18 18" stroke="#135a3f" stroke-width="6" stroke-linecap="round"/><path d="M40 52V30M40 38l-6-5M40 38l6-5M40 45l-6-5M40 45l6-5" stroke="#f4b400" stroke-width="2.5"/></svg>
  <h3>QUALITÄTS-<br>PRÜFUNG</h3>
  <p>Regelmäßige und konsequente Untersuchung unserer Futtermittel</p>
</div>
<div class="abs feature" style="left:594px;top:2572px">
  <svg width="90" height="90" viewBox="0 0 90 90" fill="none" stroke="#f4b400" stroke-width="3.5"><path d="M45 82 L10 46 A20 20 0 0 1 45 16 A20 20 0 0 1 80 46 Z"/><path d="M30 50l10 10M36 44l12 12M44 40l10 10M45 16l-10 12 8 4 10-6"/></svg>
  <h3>TRANSPARENTE<br>ERGEBNISSE</h3>
  <p>Wir geben die Ergebnisse an unsere Kunden und den ALF Marbach weiter</p>
</div>

<section class="abs band" style="top:2862px;height:273px">
  <h4 style="left:200px;top:38px">Vorteile</h4>
  <ul class="list" style="left:200px;top:84px">
    <li><svg width="29" height="29" viewBox="0 0 30 30"><circle cx="15" cy="15" r="13" fill="none" stroke="#3f9a5a" stroke-width="2"/><path d="M8 15l5 5 9-10" fill="none" stroke="#3f9a5a" stroke-width="2.5"/></svg><span>Wir prüfen unsere Futtermittel regelmäßig<br>auf <b>Schadstoffe</b></span></li>
    <li><svg width="29" height="29" viewBox="0 0 30 30"><circle cx="15" cy="15" r="13" fill="none" stroke="#3f9a5a" stroke-width="2"/><path d="M8 15l5 5 9-10" fill="none" stroke="#3f9a5a" stroke-width="2.5"/></svg><span>Standardmäßige <b>Rohproteinfraktionierung</b>,<br>um den <b>UDP-8 Gehalt</b> zu bestimmen</span></li>
    <li><svg width="29" height="29" viewBox="0 0 30 30"><circle cx="15" cy="15" r="13" fill="none" stroke="#3f9a5a" stroke-width="2"/><path d="M8 15l5 5 9-10" fill="none" stroke="#3f9a5a" stroke-width="2.5"/></svg><span>Die <b>Ergebnisse</b> stehen unseren Kunden, deren<br>Berater und dem ALF Marbach zur Verfügung</span></li>
  </ul>
  <ul class="list" style="left:608px;top:81px">
    <li><svg width="29" height="29" viewBox="0 0 30 30"><circle cx="15" cy="15" r="13" fill="none" stroke="#3f9a5a" stroke-width="2"/><path d="M8 15l5 5 9-10" fill="none" stroke="#3f9a5a" stroke-width="2.5"/></svg><span>Bei Bedarf können <b>Proben</b> aus einzelnen<br>Lagerbeständen untersucht werden</span></li>
    <li><svg width="29" height="29" viewBox="0 0 30 30"><circle cx="15" cy="15" r="13" fill="none" stroke="#3f9a5a" stroke-width="2"/><path d="M8 15l5 5 9-10" fill="none" stroke="#3f9a5a" stroke-width="2.5"/></svg><span>Wir bieten eine belastbare Grundlage für die<br><b>betriebsindividuelle Rationsberechnung</b></span></li>
  </ul>
</section>

<footer class="abs footer">
  <div class="mark"></div>
  <div class="brand">TALGRUND AGRARHANDEL</div>
  <div style="position:absolute;left:90px;top:191px;width:340px;text-align:center;font-size:14px;line-height:18px">Feldweg 7<br>91234 Marbach</div>
  <div class="contact" style="left:111px;top:256px"><span class="ic"><svg width="11" height="11" viewBox="0 0 24 24"><path fill="#3b2314" d="M6.6 10.8a15 15 0 0 0 6.6 6.6l2.2-2.2c.3-.3.7-.4 1-.2 1.1.4 2.3.6 3.6.6.6 0 1 .4 1 1V20c0 .6-.4 1-1 1A17 17 0 0 1 3 4c0-.6.4-1 1-1h3.5c.6 0 1 .4 1 1 0 1.3.2 2.5.6 3.6.1.3 0 .7-.2 1z"/></svg></span>09100 55 51 30</div>
  <div class="contact" style="left:111px;top:284px"><span class="ic"><svg width="11" height="11" viewBox="0 0 24 24"><rect x="6" y="2" width="12" height="20" rx="2" fill="none" stroke="#3b2314" stroke-width="2.5"/></svg></span>0170 000 11 22</div>
  <div class="contact" style="left:251px;top:256px"><span class="ic"><svg width="11" height="11" viewBox="0 0 24 24"><rect x="2" y="5" width="20" height="14" fill="none" stroke="#3b2314" stroke-width="2.5"/><path d="M2 5l10 8 10-8" fill="none" stroke="#3b2314" stroke-width="2.5"/></svg></span>info@talgrund-agrar.de</div>
  <div class="contact" style="left:251px;top:284px"><span class="ic"><svg width="11" height="11" viewBox="0 0 24 24"><circle cx="12" cy="12" r="9" fill="none" stroke="#3b2314" stroke-width="2.5"/><path d="M3 12h18M12 3c4 4 4 14 0 18M12 3c-4 4-4 14 0 18" fill="none" stroke="#3b2314" stroke-width="2"/></svg></span>www.talgrund-agrar.de</div>

  <div class="col-line" style="left:494px"></div>
  <div class="col-line" style="left:705px"></div>
  <h5 style="left:494px;top:50px;width:211px">INFORMATIONEN</h5>
  <div style="position:absolute;left:494px;top:144px;width:211px;text-align:center;font-size:14px;line-height:18px">AGB<br>Datenschutz<br>Kontakt<br>Impressum<br>Sitemap</div>
  <h5 style="left:705px;top:50px;width:495px">ÜBER UNS</h5>
  <p style="position:absolute;left:810px;top:122px;width:290px;text-align:center;font-style:italic;font-size:12px;line-height:18.5px">Wir von Talgrund Agrarhandel sind ein Familienunternehmen für Einzel- und Mischfutter. Unsere jahrelange Erfahrung durch unseren eigenen Milchviehbetrieb zeigt uns, wie wichtig hochwertige Nahrung für das Tierwohlbefinden ist. Dieses Wissen wollen wir an unsere Kunden weitergeben.</p>
</footer>

<div class="abs copyright">©2023 Talgrund Agrarhandel</div>

</body>
</html>
```